Web design for Crowdfunding site HopeWingsRally.com

We need a web design for christian crowdfunding website. Here is the challenge: We need responsive layout that is targeted first in iPad size of screen. It should also scale somehow down to iPhone size of screens. Web layout can be about the same size as iPad screen.

Screens should work so that main page scrolls not but only certain part of the screen scrolls and always one "page" at time. We can implement these "scrolls" then later with javascript but now we need only design. The challenge is to create this kind of hybrid website / app look.

Target is at first to raise funds to orphan people needing about $40 per month for their living and education. There is always some organization which takes care of these kids. Later there will be other christian missions included. At first we are looking to find monthly supporters.

You can be as creative as you want :) As you see from the look and feel sector, I am not looking any same traditional look which many "help kids" sites have. I am looking to reach now younger generation and therefore iPad and mobile are the main screen sizes.

Inspirational designs:
- https://example-gallery.test/profiles/studiofernlake/designs/482716?from=%2Fbrowse%2Fxhr%2Fdesigns%3Fcategory%3Dmobile-app-design
- http://www.artpoolhub.test/design/8261047 Clear, simple visuals
- http://www.artpoolhub.test/design/7394215 Header
- http://www.artpoolhub.test/design/6048392 Contrast in the colors, i think is powerfull

Some terms could be: Kids play, kids are learning (in the school). No static posture but living like kids are. I wonder also how we could also add little bit gaming style even though the question is of reali life of real people. Giving should be rewarding.

Target Market(s)

People who want help other people.

Industry/Entity Type

Christian

Number of Pages Required

4 page

Requirements
Must have
• Homepage. Mission page (In my wireframes it was one kid).
Nice to have
• Other pages and some idea how to scroll. 4 pages is no must. If you feel easy, please give first some draft and I give comments on that.

```html
<!DOCTYPE html>
<html lang="en">
<head>
<meta charset="utf-8">
<title>HopeWingsRally – Mission: Orphan Maria, 11y</title>
<link rel="stylesheet" href="https://fonts.googleapis.com/css2?family=Raleway:wght@400;600;700&family=Open+Sans:wght@400;600&display=swap">
<style>
  :root {
    --black: #000000;
    --panel: #0f0f0f;
    --header-line: #2a2a2a;
    --red: #e8302f;
    --yellow: #ffc000;
    --white: #ffffff;
    --text: #e6e6e6;
    --muted: #bdbdbd;
    --grey-dot: #3a3a3a;
    --avatar: #2e2e2e;
    --ring-rest: #3b3939;
    --rule: #444444;
  }
  * { box-sizing: border-box; margin: 0; padding: 0; }
  html, body { width: 1200px; height: 900px; overflow: hidden; }
  body {
    background: var(--black);
    color: var(--text);
    font-family: "Open Sans", Arial, sans-serif;
    position: relative;
  }

  /* Header */
  .site-header {
    position: absolute; left: 0; top: 0; width: 1200px; height: 79px;
    background: var(--black);
    border-bottom: 1px solid var(--header-line);
  }
  .nav-missions {
    position: absolute; left: 43px; top: 0; height: 79px;
    display: flex; align-items: center; gap: 10px;
    font-family: "Raleway", sans-serif; font-weight: 600; font-size: 17px;
    color: var(--white); text-transform: uppercase;
  }
  .nav-search { position: absolute; left: 260px; top: 30px; }
  .brand {
    position: absolute; left: 440px; top: 0; height: 79px;
    display: flex; align-items: center;
  }
  .brand-square { width: 77px; height: 79px; background: var(--red); }
  .brand-name {
    margin-left: 12px;
    font-family: "Raleway", sans-serif; font-weight: 600; font-size: 27px;
    letter-spacing: 0.5px; color: var(--white);
  }
  .account-links {
    position: absolute; right: 38px; top: 0; height: 79px;
    display: flex; align-items: center; gap: 48px;
    font-family: "Raleway", sans-serif; font-weight: 600; font-size: 17px; color: var(--white);
  }

  /* Mission column */
  .mission {
    position: absolute; left: 0; top: 80px; width: 783px; height: 744px;
    background: var(--panel);
  }
  .mission-title {
    position: absolute; left: 39px; top: 14px;
    font-family: "Raleway", sans-serif; font-weight: 700; font-size: 28px; color: var(--white);
  }
  .tabs {
    position: absolute; left: 40px; top: 65px; width: 718px; height: 54px;
    display: flex; background: var(--yellow);
  }
  .tab {
    display: flex; align-items: center; justify-content: center;
    font-family: "Raleway", sans-serif; font-weight: 700; font-size: 23px; color: var(--white);
  }
  .tab--story { width: 220px; background: var(--red); }
  .tab--updates { width: 211px; }
  .tab--comments { flex: 1; }

  .timeline {
    position: absolute; left: 39px; top: 148px; width: 36px; height: 562px;
  }
  .timeline-track {
    position: absolute; left: 13px; top: 18px; width: 10px; height: 526px;
    background: var(--grey-dot); border-radius: 5px;
  }
  .timeline-dot {
    position: absolute; left: 0; width: 36px; height: 36px; border-radius: 50%;
    background: var(--grey-dot);
  }
  .timeline-dot--start { top: 0; }
  .timeline-dot--current { top: 274px; background: var(--yellow); }
  .timeline-dot--end { top: 526px; }

  .story {
    position: absolute; left: 94px; top: 151px; width: 666px;
    font-size: 16.2px; line-height: 27px; color: var(--text);
  }
  .story p { margin-bottom: 11px; }
  .story-photo {
    width: 666px; height: 232px; margin: 14px 0 18px;
    background: radial-gradient(ellipse at 80% 40%, #fff6d6 0%, #f1d08a 30%, rgba(241,208,138,0) 60%),
                linear-gradient(100deg, #5f7a2e 0%, #9aa451 30%, #d8be7a 60%, #c7a9a0 100%);
  }

  /* Side panel */
  .sidebar {
    position: absolute; left: 783px; top: 80px; width: 417px; height: 744px;
    background: var(--black);
  }
  .kid-name {
    position: absolute; left: 30px; top: 13px;
    font-family: "Raleway", sans-serif; font-weight: 700; font-size: 23px; color: var(--white);
  }
  .kid-location {
    position: absolute; left: 30px; top: 53px;
    display: flex; align-items: center; gap: 6px; font-size: 16px; color: var(--muted);
  }
  .kid-organization { position: absolute; left: 30px; top: 87px; font-size: 16px; color: var(--muted); }

  .section-heading {
    position: absolute; left: 30px; width: 347px;
    font-family: "Raleway", sans-serif; font-weight: 700; font-size: 28px; color: var(--white);
  }
  .section-rule {
    position: absolute; left: 30px; width: 347px; height: 1px; background: var(--rule);
  }
  .section-rule::before {
    content: ""; position: absolute; left: 0; top: -4px; width: 70px; height: 8px;
    background: var(--yellow);
  }
  .support-heading { top: 128px; }
  .support-rule { top: 183px; }
  .supporters {
    position: absolute; left: 209px; top: 133px; display: flex; gap: 2px; align-items: center;
  }
  .supporter {
    width: 35px; height: 35px; border-radius: 50%; background: var(--avatar);
    display: flex; align-items: center; justify-content: center;
  }
  .supporters-next { margin-left: 12px; }

  .my-support {
    position: absolute; left: 30px; top: 201px;
    display: flex; align-items: center;
    font-family: "Raleway", sans-serif; font-weight: 600; font-size: 17px; color: var(--white);
  }
  .support-cancel {
    margin-left: 14px; width: 30px; height: 30px; border-radius: 50%;
    background: var(--avatar); color: var(--white);
    display: flex; align-items: center; justify-content: center; font-size: 16px; font-weight: 400;
  }
  .progress { position: absolute; left: 31px; top: 240px; }
  .progress-summary { position: absolute; left: 154px; top: 246px; }
  .progress-given {
    font-family: "Raleway", sans-serif; font-weight: 700; font-size: 21px; color: var(--white);
  }
  .progress-total { margin-top: 6px; font-size: 16px; color: var(--muted); }
  .progress-period { margin-top: 4px; display: flex; align-items: center; gap: 10px; font-size: 16px; color: var(--muted); }

  .participate-heading { top: 370px; }
  .participate-rule { top: 423px; }
  .pledges {
    position: absolute; left: 32px; top: 451px; width: 345px;
    list-style: none; display: flex; flex-direction: column; gap: 7px;
  }
  .pledge {
    height: 47px; background: var(--yellow);
    display: flex; align-items: center; padding: 0 12px 0 14px;
    font-size: 16px; color: var(--white);
  }
  .pledge:nth-child(4), .pledge:nth-child(5) { margin-top: -1px; }
  .pledge-check { width: 35px; height: 35px; background: var(--white); margin-right: 10px; flex: none; }
  .pledge-label { flex: 1; }
  .pledge-amount {
    flex: none; margin-right: 22px; padding: 2px 12px;
    border: 1px dashed var(--white); font-size: 16px;
  }

  /* Footer */
  .site-footer {
    position: absolute; left: 0; top: 824px; width: 1200px; height: 76px; background: var(--black);
  }
  .copyright { position: absolute; left: 43px; top: 26px; font-size: 16.5px; color: var(--muted); }
  .social { position: absolute; left: 973px; top: 18px; display: flex; gap: 11px; list-style: none; }
  .social-link {
    width: 41px; height: 41px; border-radius: 50%; border: 2px solid #8a8a8a;
  }
</style>
</head>
<body>

<header class="site-header">
  <div class="nav-missions">
    <svg width="16" height="14" viewBox="0 0 16 14" aria-hidden="true" fill="#fff">
      <rect x="0" y="1" width="3" height="3"/><rect x="5" y="1" width="11" height="3"/>
      <rect x="0" y="6" width="3" height="3"/><rect x="5" y="6" width="11" height="3"/>
      <rect x="0" y="11" width="3" height="3"/><rect x="5" y="11" width="11" height="3"/>
    </svg>
    See the missions
  </div>
  <svg class="nav-search" width="20" height="20" viewBox="0 0 20 20" aria-label="Search" role="img">
    <circle cx="8" cy="8" r="6" fill="none" stroke="#fff" stroke-width="3"/>
    <line x1="12.5" y1="12.5" x2="18" y2="18" stroke="#fff" stroke-width="3.5" stroke-linecap="round"/>
  </svg>
  <div class="brand">
    <div class="brand-square"></div>
    <span class="brand-name">HOPEWINGSRALLY</span>
  </div>
  <nav class="account-links">
    <span>LOGIN</span>
    <span>SIGN UP</span>
  </nav>
</header>

<main class="mission">
  <h1 class="mission-title">Mission: Orphan Maria, 11y</h1>
  <div class="tabs">
    <div class="tab tab--story">Story</div>
    <div class="tab tab--updates">Updates</div>
    <div class="tab tab--comments">Comments</div>
  </div>

  <div class="timeline" aria-hidden="true">
    <div class="timeline-track"></div>
    <div class="timeline-dot timeline-dot--start"></div>
    <div class="timeline-dot timeline-dot--current"></div>
    <div class="timeline-dot timeline-dot--end"></div>
  </div>

  <article class="story">
    <p>Lorem ipsum dolor sit amet, consectetur adipiscing elit, sed do eiusmod tempor incidi-dunt ut labore et dolore mag na aliqua. Ut enim ad minim veniam, quis nostrud exerci-tation ullamco laboris nisi ut aliquip ex ea commodo consequat.</p>
    <p>Duis aute irure dolor in reprehenderit in voluptate velit elosorem ipsum dolor sit amet, co nsectetur adipiscing elit, sed do eiusmod tempor incididunt ut labore.</p>
    <div class="story-photo" role="img" aria-label="Photo of a young green plant sprouting from a glass jar filled with coins, soft sunlit background"></div>
    <p>Lorem ipsum dolor sit amet, consectetur adipiscing elit, sed do eiusmod tempor incidi-dunt ut labore et dolore mag na aliqua. Ut enim ad minim veniam, quis nostrud exerci-tation ullamco laboris nisi ut aliquip ex ea commodo consequatute irure dolor in repre-henderit in voluptate velit elosorem ipsum dolor sit amet, co nsectetur adipiscing elit, sed do eiusmod tempor incididunt ut labore.</p>
  </article>
</main>

<aside class="sidebar">
  <h2 class="kid-name">Name: Maria, 11y</h2>
  <div class="kid-location">
    <svg width="11" height="16" viewBox="0 0 11 16" aria-hidden="true">
      <path d="M5.5 0C2.5 0 0 2.4 0 5.4 0 9.5 5.5 16 5.5 16S11 9.5 11 5.4C11 2.4 8.5 0 5.5 0z" fill="#bdbdbd"/>
      <circle cx="5.5" cy="5.4" r="2" fill="#000"/>
    </svg>
    Kalkutta
  </div>
  <div class="kid-organization">Organizatio: Jacob</div>

  <h3 class="section-heading support-heading">Support</h3>
  <div class="supporters">
    <div class="supporter"><svg width="14" height="16" viewBox="0 0 14 16" aria-hidden="true" fill="#fff"><circle cx="7" cy="4.5" r="4"/><path d="M0 16c0-4.5 3-7 7-7s7 2.5 7 7z"/></svg></div>
    <div class="supporter"><svg width="14" height="16" viewBox="0 0 14 16" aria-hidden="true" fill="#fff"><circle cx="7" cy="4.5" r="4"/><path d="M0 16c0-4.5 3-7 7-7s7 2.5 7 7z"/></svg></div>
    <div class="supporter"><svg width="14" height="16" viewBox="0 0 14 16" aria-hidden="true" fill="#fff"><circle cx="7" cy="4.5" r="4"/><path d="M0 16c0-4.5 3-7 7-7s7 2.5 7 7z"/></svg></div>
    <div class="supporter"><svg width="14" height="16" viewBox="0 0 14 16" aria-hidden="true" fill="#fff"><circle cx="7" cy="4.5" r="4"/><path d="M0 16c0-4.5 3-7 7-7s7 2.5 7 7z"/></svg></div>
    <svg class="supporters-next" width="12" height="18" viewBox="0 0 12 18" aria-label="More supporters" role="img">
      <path d="M2 2l7 7-7 7" fill="none" stroke="#fff" stroke-width="3"/>
    </svg>
  </div>
  <div class="section-rule support-rule"></div>

  <div class="my-support">My Support is now: $5/month <span class="support-cancel">x</span></div>

  <svg class="progress" width="108" height="108" viewBox="0 0 108 108" role="img" aria-label="45 percent funded">
    <circle cx="54" cy="54" r="44" fill="none" stroke="var(--ring-rest)" stroke-width="16"/>
    <circle cx="54" cy="54" r="44" fill="none" stroke="var(--red)" stroke-width="16"
            stroke-dasharray="124.4 152.1" transform="rotate(-90 54 54)"/>
    <text x="54" y="61" text-anchor="middle" fill="#fff" font-family="Raleway, sans-serif" font-weight="700" font-size="22">45%</text>
  </svg>
  <div class="progress-summary">
    <div class="progress-given">$15 given</div>
    <div class="progress-total">of total $35 needed</div>
    <div class="progress-period">
      <svg width="17" height="20" viewBox="0 0 17 20" aria-hidden="true" fill="none" stroke="#bdbdbd" stroke-width="1.6">
        <rect x="1" y="1" width="15" height="18"/><line x1="3.5" y1="5" x2="13.5" y2="5"/>
        <path d="M4 9h2M8 9h2M12 9h1.5M4 12h2M8 12h2M12 12h1.5M4 15h2M8 15h2M12 15h1.5"/>
      </svg>
      per month need
    </div>
  </div>

  <h3 class="section-heading participate-heading">Participate</h3>
  <div class="section-rule participate-rule"></div>

  <ul class="pledges">
    <li class="pledge"><span class="pledge-check"></span><span class="pledge-label">I am in,, $1/ month</span>
      <svg width="15" height="14" viewBox="0 0 15 14" aria-hidden="true" fill="#fff"><path d="M0 1h3l2 7h8l2-6H4.3L4 1z"/><circle cx="6" cy="11.5" r="1.5"/><circle cx="12" cy="11.5" r="1.5"/></svg></li>
    <li class="pledge"><span class="pledge-check"></span><span class="pledge-label">Increased, $35/ month</span>
      <svg width="15" height="14" viewBox="0 0 15 14" aria-hidden="true" fill="#fff"><path d="M0 1h3l2 7h8l2-6H4.3L4 1z"/><circle cx="6" cy="11.5" r="1.5"/><circle cx="12" cy="11.5" r="1.5"/></svg></li>
    <li class="pledge"><span class="pledge-check"></span><span class="pledge-label">Decent help, $35/ month</span>
      <svg width="15" height="14" viewBox="0 0 15 14" aria-hidden="true" fill="#fff"><path d="M0 1h3l2 7h8l2-6H4.3L4 1z"/><circle cx="6" cy="11.5" r="1.5"/><circle cx="12" cy="11.5" r="1.5"/></svg></li>
    <li class="pledge"><span class="pledge-check"></span><span class="pledge-label">Whole kid, $35/ month</span>
      <svg width="15" height="14" viewBox="0 0 15 14" aria-hidden="true" fill="#fff"><path d="M0 1h3l2 7h8l2-6H4.3L4 1z"/><circle cx="6" cy="11.5" r="1.5"/><circle cx="12" cy="11.5" r="1.5"/></svg></li>
    <li class="pledge"><span class="pledge-check"></span><span class="pledge-label">My Amount</span><span class="pledge-amount">Enter Amount</span>
      <svg width="15" height="14" viewBox="0 0 15 14" aria-hidden="true" fill="#fff"><path d="M0 1h3l2 7h8l2-6H4.3L4 1z"/><circle cx="6" cy="11.5" r="1.5"/><circle cx="12" cy="11.5" r="1.5"/></svg></li>
  </ul>
</aside>

<footer class="site-footer">
  <p class="copyright">© 2016 Hopewingsrally. All rights reserved.Privacy &amp; Legal Policy</p>
  <ul class="social" aria-label="Social links">
    <li class="social-link"></li>
    <li class="social-link"></li>
    <li class="social-link"></li>
    <li class="social-link"></li>
  </ul>
</footer>

</body>
</html>
```